HOT TUB - SPAS service needs an business card

I need an business for my company who his specialise in a maintenance,water treatment and cleaning of Hot Tub - Spas for commercial and residential customers. The company operate mainly in the ski resort of Chamonix, Megève and St Gervais. The final product should communicate pure water, cleanest and professional for luxury property's.
I have upload a logo but any improvement on it is welcome.(color,size, details etc..) or any other idea. Thank you
Company Name: 58 BAINS
My name: Lucien Marchetti
Email: lucimarch@examplemail.net
Tel: +33 (0)6 71 58 29 64
Description to be on the card in french(first langage) and in English:
- Spas service
- Entretien, traitement eau, nettoyage.
- Maintenance, water treatment, cleaning.
Industry/Entity Type
Residential
Colors
Designer to choose colors to be used in the design.
Look and feel
Each slider illustrates characteristics of the customer's brand and the style your logo design should communicate.

```html
<!DOCTYPE html>
<html lang="fr">
<head>
<meta charset="utf-8">
<title>58 BAINS – Cartes de visite</title>
<link rel="stylesheet" href="https://fonts.googleapis.com/css2?family=Source+Sans+3:wght@400;600;700&display=swap">
<style>
  :root {
    --page-bg: #eef1f4;
    --card-blue: #22a7fe;
    --band-dark: #0d63cf;
    --band-light: #a9dcfd;
    --logo-tint: #4cb8fe;
    --ink-white: #ffffff;
    --divider: rgba(255, 255, 255, 0.55);
  }
  * { margin: 0; padding: 0; box-sizing: border-box; }
  html, body {
    width: 1200px;
    height: 1056px;
    overflow: hidden;
    background: var(--page-bg);
    font-family: "Source Sans 3", "Myriad Pro", Arial, sans-serif;
    color: var(--ink-white);
  }
  .canvas { position: relative; width: 1200px; height: 1056px; }

  .card {
    position: absolute;
    width: 814px;
    height: 465px;
    border-radius: 24px;
    background: var(--card-blue);
    overflow: hidden;
  }
  .card--front { left: 38px; top: 33px; }
  .card--back { left: 322px; top: 545px; }

  .logo-area {
    position: absolute;
    display: flex;
    align-items: center;
    justify-content: center;
    background: linear-gradient(180deg, var(--card-blue), var(--logo-tint));
    border-radius: 6px;
  }
  .logo-area__name {
    font-weight: 600;
    font-size: 46px;
    letter-spacing: 2px;
    color: var(--ink-white);
  }
  .card--front .logo-area { left: 152px; top: 67px; width: 520px; height: 143px; }
  .card--back .logo-area { left: 103px; top: 91px; width: 623px; height: 169px; }

  .holder-name {
    position: absolute;
    left: 82px;
    top: 290px;
    font-weight: 700;
    font-size: 28px;
    line-height: 34px;
  }
  .contact-divider {
    position: absolute;
    left: 363px;
    top: 267px;
    width: 1.5px;
    height: 76px;
    background: var(--divider);
  }
  .contact {
    position: absolute;
    left: 386px;
    display: flex;
    align-items: center;
    font-size: 27px;
    line-height: 32px;
  }
  .contact--phone { top: 271px; font-weight: 600; }
  .contact--email { top: 313px; }
  .contact__icon { width: 24px; height: 24px; margin-right: 10px; flex: none; }
  .contact--email .contact__icon { margin-right: 16px; }

  .card-band { position: absolute; left: 0; top: 0; width: 814px; height: 465px; }
  .company-name {
    position: absolute;
    left: 372px;
    right: 0;
    top: 406px;
    text-align: center;
    font-weight: 700;
    font-size: 39px;
    line-height: 48px;
    padding-left: 0;
  }

  .services-title {
    position: absolute;
    left: 0; right: 0;
    top: 322px;
    text-align: center;
    font-weight: 700;
    font-size: 28px;
    line-height: 36px;
  }
  .services-line {
    position: absolute;
    left: 0; right: 0;
    text-align: center;
    font-size: 29px;
    line-height: 36px;
    word-spacing: 1px;
  }
  .services-line--fr { top: 369px; }
  .services-line--en { top: 408px; }
</style>
</head>
<body>
<main class="canvas">

  <section class="card card--front" aria-label="Recto de la carte">
    <div class="logo-area" role="img" aria-label="Logo 58 BAINS : montagnes, chalet et canalisation du spa">
      <span class="logo-area__name">58 BAINS</span>
    </div>

    <p class="holder-name">Lucien Marchetti</p>
    <div class="contact-divider"></div>

    <p class="contact contact--phone">
      <svg class="contact__icon" viewBox="0 0 24 24" aria-hidden="true">
        <circle cx="12" cy="12" r="10.5" fill="none" stroke="#fff" stroke-width="1.6"/>
        <path d="M8.6 6.8c.5-.4 1.1-.3 1.4.2l1 1.7c.3.5.1 1-.3 1.3l-.7.5c.4 1.3 1.4 2.6 2.6 3.4l.6-.6c.4-.4 1-.4 1.4 0l1.5 1.2c.4.4.4 1 0 1.4-1.3 1.3-2.9 1.3-4.6 0-2.2-1.6-3.7-3.8-4-6.2-.1-1.1.4-2.2 1.1-2.9z" fill="#fff"/>
      </svg>
      +33 (0)6 71 58 29 64
    </p>
    <p class="contact contact--email">
      <svg class="contact__icon" viewBox="0 0 24 24" aria-hidden="true">
        <path d="M2 9l10-6 10 6v11H2z" fill="#fff"/>
        <path d="M2 9l10 7 10-7" fill="none" stroke="var(--card-blue)" stroke-width="1.6"/>
      </svg>
      lucimarch@examplemail.net
    </p>

    <svg class="card-band" viewBox="0 0 814 465" aria-hidden="true">
      <polygon points="0,399 357,399 334,422 0,422" fill="var(--band-light)"/>
      <polygon points="372,397 814,397 814,465 0,465 0,437 336,437" fill="var(--band-dark)"/>
    </svg>
    <p class="company-name">58 BAINS</p>
  </section>

  <section class="card card--back" aria-label="Verso de la carte">
    <div class="logo-area" role="img" aria-label="Logo 58 BAINS : montagnes, chalet et canalisation du spa">
      <span class="logo-area__name">58 BAINS</span>
    </div>
    <h2 class="services-title">SPAS SERVICES</h2>
    <p class="services-line services-line--fr">•Entretien &nbsp;•traitement eau &nbsp;•nettoyage</p>
    <p class="services-line services-line--en">•Maintenance &nbsp;•water treatment &nbsp;•cleaning.</p>
  </section>

</main>
</body>
</html>
```